Brindle Recycling needs a new web design

We need a new web design for our company based in Austin, TX. We resell and recycling electronics such as laptops, computer components, Zelvotabs, Quorns, etc. Since our inception over ten years ago, we’ve become one of the premier electronics recycling and remarketing companies in Austin, Texas.

```html
<!DOCTYPE html>
<html lang="en">
<head>
<meta charset="utf-8">
<title>Brindle Recycling</title>
<link href="https://fonts.googleapis.com/css2?family=Barlow:wght@400;500;600;700&family=Poppins:wght@400;500&display=swap" rel="stylesheet">
<style>
:root{
  --blue:#1a70c0;
  --green:#2fb10a;
  --navy:#0e2232;
  --ink:#1d1d1d;
  --text:#333;
  --muted:#666;
  --panel-dark:#1b1b1b;
  --footer:#1c1c1c;
  --light:#f1f1f1;
  --white:#fff;
  --hero-top:#6fa3d4;
  --hero-bottom:#a9c9e4;
  --bin:#a4acb0;
}
*{box-sizing:border-box;margin:0;padding:0}
html,body{width:1200px;height:2233px;overflow:hidden}
body{font-family:"Barlow",Arial,sans-serif;color:var(--text);background:var(--white);position:relative}
a{color:inherit;text-decoration:none}

/* header */
.site-header{position:absolute;top:0;left:0;width:1200px;height:83px;background:var(--white)}
.brand{position:absolute;left:210px;top:22px;display:flex;align-items:center;gap:8px}
.brand-dot{width:38px;height:38px;border-radius:50%;background:var(--navy)}
.brand-name{font-family:"Barlow",sans-serif;font-weight:700;font-size:22px;color:var(--blue);line-height:1}
.header-phone{position:absolute;left:700px;top:27px;display:flex;align-items:center;gap:8px;font-weight:600;font-size:22px;color:var(--ink)}
.btn{display:inline-flex;align-items:center;justify-content:center;border-radius:17px;color:var(--white);font-weight:500;font-size:12px;height:33px}
.btn-blue{background:var(--blue)}
.btn-green{background:var(--green)}
.btn-book{position:absolute;left:884px;top:25px;width:106px;height:33px}

/* nav */
.main-nav{position:absolute;top:83px;left:0;width:1200px;height:38px;background:var(--navy)}
.nav-list{position:absolute;left:210px;top:0;display:flex;list-style:none;height:38px}
.nav-list li{display:flex;align-items:center;padding:0 18px;color:var(--white);font-size:12px;font-weight:500;letter-spacing:.3px}
.nav-list li.is-active{background:var(--blue)}
.nav-search{position:absolute;left:833px;top:6px;width:157px;height:26px;border-radius:13px;background:var(--white);font-size:11px;color:#999;padding:6px 12px}
.nav-search svg{position:absolute;right:9px;top:7px}

/* hero */
.hero{position:absolute;top:121px;left:0;width:1200px;height:475px;overflow:hidden}
.hero-scene{position:absolute;inset:0;background:linear-gradient(180deg,var(--hero-top),var(--hero-bottom))}
.hero-bin{position:absolute;left:735px;top:70px;width:200px;height:340px;border-radius:24px;background:var(--bin)}
.hero-copy{position:absolute;left:209px;top:140px}
.hero-title{font-weight:700;font-size:31px;color:var(--ink);white-space:nowrap}
.hero-title span{color:var(--blue)}
.hero-text{margin-top:16px;width:450px;font-size:15px;line-height:22px;color:#2a2a2a}
.hero-actions{position:absolute;left:209px;top:256px;display:flex;gap:10px}
.hero-actions .btn{width:146px}
.hero-arrow{position:absolute;top:199px;width:37px;height:37px;border-radius:50%;background:rgba(40,40,40,.75);display:flex;align-items:center;justify-content:center}

/* feature panels */
.features{position:absolute;top:596px;left:0;width:1200px;height:300px;display:flex}
.feature{width:400px;height:300px;color:var(--white);text-align:center;padding-top:52px}
.feature-blue{background:var(--blue)}
.feature-green{background:var(--green)}
.feature-dark{background:var(--panel-dark)}
.feature h3{font-size:19px;font-weight:600;margin-top:14px}
.feature p{font-size:11.5px;line-height:19px;margin:15px auto 0;width:290px}
.btn-white{display:inline-flex;align-items:center;justify-content:center;margin-top:22px;width:122px;height:33px;border-radius:17px;background:var(--white);color:var(--ink);font-size:11.5px;font-weight:500}

/* about */
.about{position:absolute;top:896px;left:0;width:1200px;height:434px}
.about-col{position:absolute;top:50px}
.about-col h2{font-size:22px;font-weight:600;color:var(--ink);white-space:nowrap}
.about-lead{margin-top:18px;font-size:12.5px;line-height:19px;color:#333}
.about-body{margin-top:16px;font-size:11px;line-height:19px;color:var(--muted)}
.about-divider{position:absolute;left:599px;top:55px;width:1px;height:200px;background:#e2e2e2}
.about-cta{position:absolute;top:302px;left:0;width:1200px;text-align:center;font-size:17px;color:var(--ink)}
.about-actions{position:absolute;top:347px;left:0;width:1200px;display:flex;justify-content:center;gap:8px}
.about-actions .btn{width:148px}

/* products */
.products{position:absolute;top:1330px;left:0;width:1200px;height:516px;background:var(--light)}
.products h2{position:absolute;top:52px;width:1200px;text-align:center;font-size:21px;font-weight:600;color:var(--ink)}
.products-bin{position:absolute;left:500px;top:130px;width:192px;height:330px;border-radius:24px;background:var(--bin)}
.product{position:absolute;width:120px;height:120px;color:var(--white);font-size:11.5px;font-weight:500;display:flex;flex-direction:column;align-items:center;justify-content:center;gap:8px}
.product-blue{background:var(--blue)}
.product-dark{background:var(--panel-dark)}
.product-green{background:var(--green)}
.blob-a{border-radius:60% 40% 55% 45%/45% 55% 45% 55%}
.blob-b{border-radius:45% 55% 40% 60%/55% 45% 55% 45%}

/* certifications */
.certs{position:absolute;top:1846px;left:0;width:1200px;height:119px;background:var(--white)}
.certs-label{position:absolute;left:258px;top:46px;font-family:"Poppins",sans-serif;font-size:16px;color:#444}
.cert-badge{position:absolute;top:30px;height:58px}

/* footer */
.site-footer{position:absolute;top:1965px;left:0;width:1200px;height:268px;background:var(--footer);color:#d7d7d7}
.footer-col{position:absolute;top:38px}
.footer-col h4{font-size:12.5px;font-weight:600;color:var(--white);letter-spacing:.3px;margin-bottom:14px}
.footer-col li{list-style:none;font-size:11px;line-height:19px}
.footer-col p{font-size:11px;line-height:17px}
.footer-brand{position:absolute;right:210px;top:40px;display:flex;align-items:center;gap:8px}
.footer-brand .brand-dot{width:32px;height:32px;background:var(--white)}
.footer-brand .brand-name{color:var(--white);font-size:20px}
.social{position:absolute;right:210px;top:113px;display:flex;gap:5px}
.social span{width:20px;height:20px;background:var(--white)}
.copyright{position:absolute;left:210px;top:219px;font-size:10.5px;color:#bdbdbd}
.contact-tab{position:absolute;left:870px;top:235px;width:120px;height:33px;background:var(--white);color:var(--ink);font-size:12px;font-weight:600;display:flex;align-items:center;justify-content:center;gap:6px;border-radius:3px 3px 0 0}
</style>
</head>
<body>

<header class="site-header">
  <div class="brand"><span class="brand-dot"></span><span class="brand-name">Brindle Recycling</span></div>
  <div class="header-phone">
    <svg width="18" height="18" viewBox="0 0 24 24"><path fill="#1a70c0" d="M6.6 10.8a15.1 15.1 0 0 0 6.6 6.6l2.2-2.2c.3-.3.7-.4 1-.2 1.1.4 2.3.6 3.6.6.6 0 1 .4 1 1V20c0 .6-.4 1-1 1A17 17 0 0 1 3 4c0-.6.4-1 1-1h3.5c.6 0 1 .4 1 1 0 1.3.2 2.5.6 3.6.1.3 0 .7-.2 1z"/></svg>
    (512) 555-0147
  </div>
  <a class="btn btn-blue btn-book" href="#">Book Online</a>
</header>

<nav class="main-nav">
  <ul class="nav-list">
    <li class="is-active">HOME</li><li>ABOUT</li><li>SERVICES</li><li>CERTIFICATIONS</li><li>NEWS</li><li>CONTACT</li>
  </ul>
  <div class="nav-search">Search
    <svg width="11" height="11" viewBox="0 0 24 24"><circle cx="10" cy="10" r="7" fill="none" stroke="#333" stroke-width="2.5"/><path d="M15 15l6 6" stroke="#333" stroke-width="2.5"/></svg>
  </div>
</nav>

<section class="hero">
  <div class="hero-scene" role="img" aria-label="Photo area: sunny sky with clouds above a wide green grass field"></div>
  <div class="hero-bin" role="img" aria-label="Illustration area: glass recycling bin filled with old computers and devices"></div>
  <div class="hero-copy">
    <h1 class="hero-title"><span>Recycling Today</span> Reuse Tomorrow</h1>
    <p class="hero-text">We resell and recycling electronics such as laptops, computer components, Zelvotabs, Quorns, etc.</p>
  </div>
  <div class="hero-actions">
    <a class="btn btn-blue" href="#">Schedule A Pickup</a>
    <a class="btn btn-green" href="#">Call (512) 555-0147</a>
  </div>
  <span class="hero-arrow" style="left:76px"><svg width="12" height="12" viewBox="0 0 24 24"><path d="M15 4l-8 8 8 8" fill="none" stroke="#fff" stroke-width="3"/></svg></span>
  <span class="hero-arrow" style="left:1086px"><svg width="12" height="12" viewBox="0 0 24 24"><path d="M9 4l8 8-8 8" fill="none" stroke="#fff" stroke-width="3"/></svg></span>
</section>

<section class="features">
  <div class="feature feature-blue">
    <svg width="44" height="40" viewBox="0 0 44 40" fill="#fff"><path d="M22 2l7 11-4 2-3-5-4 7-5-3z"/><path d="M40 30l-6 10h-8v-5h6l-4-7 5-3z"/><path d="M4 30l6-10-4-2 12-1 2 11-4-2-4 7h8v5H8z"/></svg>
    <h3>Electronic Recycling</h3>
    <p>At Brindle Recycling, we strive to keep the environment clean through our wide range of services.</p>
    <a class="btn-white" href="#">Find Out More</a>
  </div>
  <div class="feature feature-green">
    <svg width="44" height="40" viewBox="0 0 44 40" fill="#fff"><path d="M2 10h26v20H2z"/><path d="M30 16h7l5 7v7H30z"/><circle cx="10" cy="32" r="4" stroke="#2fb10a" stroke-width="2"/><circle cx="35" cy="32" r="4" stroke="#2fb10a" stroke-width="2"/><path d="M15 14l3 5h-6z" fill="#2fb10a"/></svg>
    <h3>Recycling Pickup</h3>
    <p>At Brindle Recycling, we go out of our way to make sure your recycling process is made easy as possible.</p>
    <a class="btn-white" href="#">Find Out More</a>
  </div>
  <div class="feature feature-dark">
    <svg width="44" height="40" viewBox="0 0 44 40" fill="#fff"><path d="M22 2l7 11-4 2-3-5-4 7-5-3z"/><path d="M40 30l-6 10h-8v-5h6l-4-7 5-3z"/><path d="M4 30l6-10-4-2 12-1 2 11-4-2-4 7h8v5H8z"/></svg>
    <h3>Contact Us</h3>
    <p>Get in touch with Brindle Recycling, and learn more about the wide range of recycling services.</p>
    <a class="btn-white" href="#">Find Out More</a>
  </div>
</section>

<section class="about">
  <div class="about-col" style="left:210px;width:318px">
    <h2>About Brindle Recycling</h2>
    <p class="about-lead">At Brindle Recycling, we're committed to providing environmentally friendly recycling solutions to Austin and the surrounding areas.</p>
    <p class="about-body">Founded in 2006, our mission is to process your materials in a safe, non-hazardous manner — with an aim to keep the world environmentally clean. As a TR5 recycling center, we believe in promoting smart recycling habits in order to achieve long lasting results.</p>
  </div>
  <div class="about-divider"></div>
  <div class="about-col" style="left:666px;width:300px">
    <h2>Computer Recycling Made Easy</h2>
    <p class="about-lead">Want to make a difference to our environment and planet? Brindle Recycling is here to help! Brindle recycling has been helping keep the environment healthy since 2006.</p>
    <p class="about-body">we specialize in recycling services that help citizens become experts at reducing waste. We have a passion to keep our world clean and are here to guide you through all the stages of the recycling process.</p>
  </div>
  <p class="about-cta">Do you have any computer or electronic equipment to recycling of?</p>
  <div class="about-actions">
    <a class="btn btn-blue" href="#">Schedule A Pickup</a>
    <a class="btn btn-green" href="#">Call (512) 555-0147</a>
  </div>
</section>

<section class="products">
  <h2>Recycling Products</h2>
  <div class="products-bin" role="img" aria-label="Illustration area: glass recycling bin overflowing with discarded electronics"></div>

  <div class="product product-blue blob-a" style="left:210px;top:166px">
    <svg width="34" height="30" viewBox="0 0 34 30" fill="none" stroke="#fff" stroke-width="2"><rect x="2" y="2" width="30" height="20"/><path d="M12 28h10M17 22v6"/></svg>Computers</div>
  <div class="product product-dark blob-b" style="left:346px;top:159px">
    <svg width="34" height="30" viewBox="0 0 34 30" fill="none" stroke="#fff" stroke-width="2"><rect x="6" y="4" width="22" height="16"/><path d="M2 24h30"/></svg>Laptops</div>
  <div class="product product-green blob-b" style="left:300px;top:293px">
    <svg width="34" height="30" viewBox="0 0 34 30" fill="none" stroke="#fff" stroke-width="2"><rect x="4" y="8" width="16" height="20" rx="8"/><path d="M12 8v7M12 8c0-4 6-6 10-4"/></svg>Small Devices</div>
  <div class="product product-dark blob-a" style="left:734px;top:159px">
    <svg width="34" height="30" viewBox="0 0 34 30" fill="none" stroke="#fff" stroke-width="2"><rect x="2" y="2" width="30" height="20"/><path d="M12 28h10M17 22v6"/></svg>Quorns</div>
  <div class="product product-blue blob-b" style="left:871px;top:166px">
    <svg width="34" height="30" viewBox="0 0 34 30" fill="none" stroke="#fff" stroke-width="2"><rect x="4" y="4" width="16" height="24" rx="2"/><path d="M20 10a10 10 0 0 1 0 14"/><circle cx="12" cy="12" r="2"/></svg>Components</div>
  <div class="product product-green blob-a" style="left:822px;top:285px">
    <svg width="34" height="30" viewBox="0 0 34 30" fill="none" stroke="#fff" stroke-width="2"><rect x="8" y="2" width="18" height="26" rx="2"/><path d="M15 24h4"/></svg>Zelvotabs</div>
</section>

<section class="certs">
  <p class="certs-label">Certified Recyclers</p>
  <span class="cert-badge" style="left:493px;width:84px;background:#d9dde6"></span>
  <span class="cert-badge" style="left:620px;width:85px;border-radius:50%;background:#2c4e9c"></span>
  <span class="cert-badge" style="left:770px;width:64px;top:27px;height:64px;border-radius:50%;border:2px solid #777"></span>
  <span class="cert-badge" style="left:875px;width:115px;background:#dff0d4;border-radius:6px"></span>
</section>

<footer class="site-footer">
  <div class="footer-col" style="left:210px">
    <h4>CONTACT INFO</h4>
    <p>1420 Larkspur Bend Blvd<br>Austin TX USA 78799</p>
    <p style="margin-top:18px">(512) 555-0147<br>mara@brindlerecycling.com</p>
  </div>
  <div class="footer-col" style="left:442px">
    <h4>QUICK LINKS</h4>
    <ul><li>Home</li><li>About</li><li>Services</li><li>Certifications</li><li>News</li><li>Contact</li></ul>
  </div>
  <div class="footer-col" style="left:603px">
    <h4>HELPFUL LINKS</h4>
    <ul><li>Service Area</li><li>News</li><li>Terms of Use</li><li>Privacy Policy</li><li>Sitemap</li></ul>
  </div>
  <div class="footer-brand"><span class="brand-dot"></span><span class="brand-name">Brindle Recycling</span></div>
  <div class="social"><span></span><span></span><span></span></div>
  <p class="copyright">©2018 by Brindle Recycling. All Rights Reserved</p>
  <a class="contact-tab" href="#">
    <svg width="14" height="10" viewBox="0 0 14 10"><rect width="14" height="10" fill="#1d1d1d"/><path d="M0 0l7 5 7-5" fill="none" stroke="#fff" stroke-width="1.2"/></svg>CONTACT US</a>
</footer>

</body>
</html>
```